Belmont Ridge Business Card Design Project

We have recently rebranded and would like to design new business cards that incorporate the corporate logo - double sided cards with corporate logo on one side and contact details on the other

Target Market(s)

Sophisticated and high net worth investors and finance industry professionals

Industry/Entity Type

Funds Management

Contact Information for Business Card

The card should prominently feature the company name and logo. Other details will be standard contact details for each staff member - name, address, phone, email, website

Colors
0054AA
0677BA
7BADD7
CADEEF
E8F1F8

Requirements
Must have
• Double-sided design with one side prominently featuring the corporate logo and the other side with all standard contact details

```html
<!DOCTYPE html>
<html lang="en">
<head>
<meta charset="utf-8">
<title>Belmont Ridge – Business Card</title>
<link rel="stylesheet" href="https://fonts.googleapis.com/css2?family=Cinzel:wght@500;600&family=Libre+Baskerville&display=swap">
<style>
  :root {
    --backdrop: #2b2b2b;
    --navy: #1f4170;
    --paper: #ffffff;
    --ink-light: #ffffff;
    --ink-soft: #e8f1f8;
  }
  * { margin: 0; padding: 0; box-sizing: border-box; }
  html, body { width: 1200px; height: 689px; overflow: hidden; }
  body {
    background: var(--backdrop);
    display: flex;
    align-items: center;
    justify-content: center;
    gap: 70px;
    font-family: "Libre Baskerville", Georgia, serif;
  }
  .card { box-shadow: 0 18px 40px rgba(0,0,0,.45); }

  /* Contact side (portrait) */
  .card-contact {
    width: 300px;
    height: 525px;
    background: var(--navy);
    color: var(--ink-light);
    display: flex;
    flex-direction: column;
    align-items: center;
    justify-content: center;
    text-align: center;
  }
  .contact-brand {
    font-family: "Cinzel", "Times New Roman", serif;
    font-weight: 600;
    font-size: 15px;
    letter-spacing: 2px;
    margin-bottom: 22px;
  }
  .person-name {
    font-family: "Cinzel", "Times New Roman", serif;
    font-weight: 500;
    font-size: 24px;
    letter-spacing: 1.5px;
  }
  .person-title { font-size: 12px; margin-top: 4px; }
  .divider { width: 16px; height: 2px; background: var(--ink-light); margin: 18px 0; }
  .address { font-size: 12px; line-height: 1.55; }
  .icons { display: flex; gap: 8px; margin: 14px 0 12px; }
  .icons svg { width: 11px; height: 11px; fill: var(--ink-light); }
  .details { font-size: 12.5px; line-height: 1.6; color: var(--ink-soft); }

  /* Brand side (landscape) */
  .card-brand {
    width: 525px;
    height: 300px;
    background: var(--paper);
    color: var(--navy);
    display: flex;
    flex-direction: column;
    align-items: center;
    justify-content: center;
  }
  .brand-name {
    font-family: "Cinzel", "Times New Roman", serif;
    font-weight: 600;
    font-size: 44px;
    line-height: 1.05;
    letter-spacing: 1px;
    text-align: center;
  }
  .brand-web {
    margin-top: 26px;
    font-size: 10px;
    letter-spacing: 4px;
  }
</style>
</head>
<body>
  <section class="card card-contact">
    <div class="contact-brand">BELMONT RIDGE</div>
    <h1 class="person-name">DANIEL REYES</h1>
    <p class="person-title">Founder &amp; CEO</p>
    <div class="divider"></div>
    <p class="address">4870 Harlow Lane<br>Westbrook, CT 06498</p>
    <div class="icons" aria-hidden="true">
      <svg viewBox="0 0 12 12"><path d="M2.5 1l2 2.4-1.2 1.3a7 7 0 0 0 4 4l1.3-1.2 2.4 2-1.3 1.5C5.4 10.8 1.2 6.6 1 2.3z"/></svg>
      <svg viewBox="0 0 12 12"><path d="M3.5 0.5h5v11h-5z M4.5 1.8v7.4h3V1.8z"/></svg>
      <svg viewBox="0 0 12 12"><path d="M1 2.5h10v7H1z M1.8 3.2 6 6.4l4.2-3.2z" fill-rule="evenodd"/></svg>
      <svg viewBox="0 0 12 12"><circle cx="6" cy="6" r="5"/></svg>
    </div>
    <p class="details">(555) 318-2046<br>(555) 318-2047<br>info@belmontridge.com<br>belmontridge.com</p>
  </section>

  <section class="card card-brand">
    <div class="brand-name">BELMONT<br>RIDGE</div>
    <p class="brand-web">www.BelmontRidge.com</p>
  </section>
</body>
</html>
```